Dwelvano - "Where Pest Control is Free for Life..." Please see pitch deck...

Project goal, that this is a reusable template, not a one-off card
Brand and design direction, follow the logo, use the brand palette (with a color swatch table), typography and layout guidance
The John Doe placeholder content as a clean field-by-field table (name, title, company, address, office, cell, fax, email, dwelvano.com)
Print specs, 3.5 × 2 in trim, 0.125 in bleed, 300 DPI, CMYK, crop marks
Deliverables, layered editable PSD (your primary ask) plus vector .AI/.EPS and a press-ready PDF/X-1a, with fonts packaged
What you'll provide (logo, colors, fonts)
Process and sign-off, concept first, then full file package on approval.
Populate every field with this John Doe placeholder data so we can see the layout fully built out. We will replace it per person.
Name John Doe
Title Title / Position
Company Dwelvano
Address 48 Harbor Lane, Suite 210, Orlando, FL 32801
Office (407) 555-0142
Cell (407) 555-0168
Fax (407) 555-0187
Email johndoe@dwelvano.com
Website dwelvano.com

We need the working, editable source files so we can update them ourselves, plus a ready-to-print export:
1. Photoshop (.PSD) — fully layered and editable, with each contact field on its own labeled text layer. This is the primary requested format.
2. Vector source — the press-standard editable format, Adobe Illustrator (.AI) and/or .EPS, since vector is preferred for crisp text and logos at print.
3. Print-ready PDF — press-quality (PDF/X-1a), CMYK, with bleed and crop marks, both sides.
4. Packaged fonts and links — include or list all fonts used, and package any linked assets so the files open correctly on our end.

Why both PSD and vector
The PSD covers our request directly and is easy for us to edit. Vector (.AI/.EPS) is what most commercial printers actually prefer for type and logos because it stays razor-sharp at any size. Providing both keeps us flexible no matter which printer we use. Have fun and keep it modern and cool the designer of the logo did a great job, see what you can do.

```html
<!DOCTYPE html>
<html lang="en">
<head>
<meta charset="utf-8">
<title>Dwelvano Business Card</title>
<link rel="stylesheet" href="https://fonts.googleapis.com/css2?family=Montserrat:ital,wght@0,400;0,700;0,800;1,400&display=swap">
<style>
  :root {
    --backdrop: #1b1c1f;
    --paper: #f3f3f3;
    --navy: #0b1226;
    --ink: #1d1f26;
    --teal: #12b3c4;
    --light: #f2f2f2;
  }
  * { margin: 0; padding: 0; box-sizing: border-box; }
  html, body { width: 1200px; height: 1059px; overflow: hidden; }
  body {
    background: var(--backdrop);
    font-family: "Montserrat", sans-serif;
    position: relative;
  }
  .card {
    position: absolute;
    width: 690px;
    height: 392px;
    border-radius: 16px;
    overflow: hidden;
  }
  .card-front { left: 256px; top: 89px; background: var(--paper); color: var(--ink); }
  .card-back  { left: 255px; top: 548px; background: var(--navy); color: var(--light); }

  /* front */
  .wordmark-front {
    position: absolute; left: 0; right: 0; top: 60px;
    text-align: center;
    font-weight: 800; font-size: 64px; letter-spacing: -2px; line-height: 1.2;
    color: var(--navy);
  }
  .identity { position: absolute; right: 372px; top: 206px; text-align: left; white-space: nowrap; }
  .person-name { font-weight: 700; font-size: 30px; color: var(--navy); line-height: 1; letter-spacing: 0.5px; }
  .person-company { font-weight: 400; font-size: 17px; margin-top: 6px; color: var(--ink); }
  .divider {
    position: absolute; left: 344px; top: 177px;
    width: 1.5px; height: 110px; background: var(--ink);
  }
  .contact-list { position: absolute; left: 372px; top: 170px; list-style: none; }
  .contact-item {
    display: flex; align-items: center; gap: 6px;
    height: 24px; font-size: 16px; color: var(--ink); white-space: nowrap;
  }
  .contact-item svg { width: 12px; height: 12px; fill: var(--teal); flex: none; }
  .address {
    position: absolute; left: 0; right: 0; top: 332px;
    text-align: center; font-size: 15.5px; color: var(--ink);
  }

  /* back */
  .wordmark-back {
    position: absolute; left: 0; right: 0; top: 108px;
    text-align: center;
    font-weight: 800; font-size: 92px; letter-spacing: -3px; line-height: 1.2;
    color: var(--light);
  }
  .tagline {
    position: absolute; left: 0; right: 0; top: 224px;
    text-align: center; font-weight: 800; font-size: 18px; letter-spacing: 2px;
  }
  .subline {
    position: absolute; left: 0; right: 0; top: 250px;
    text-align: center; font-style: italic; font-size: 16px; color: var(--teal);
  }
</style>
</head>
<body>
  <section class="card card-front">
    <div class="wordmark-front">Dwelvano</div>

    <div class="identity">
      <p class="person-name">JOHN DOE</p>
      <p class="person-company">Company Dwelvano</p>
    </div>

    <div class="divider"></div>

    <ul class="contact-list">
      <li class="contact-item">
        <svg viewBox="0 0 24 24"><path d="M6.6 10.8a15 15 0 0 0 6.6 6.6l2.2-2.2c.3-.3.7-.4 1-.2 1.1.4 2.3.6 3.6.6.6 0 1 .4 1 1V20c0 .6-.4 1-1 1A17 17 0 0 1 3 4c0-.6.4-1 1-1h3.5c.6 0 1 .4 1 1 0 1.3.2 2.5.6 3.6.1.3 0 .7-.2 1z"/></svg>
        (407) 555-0142
      </li>
      <li class="contact-item">
        <svg viewBox="0 0 24 24"><path d="M7 1h10a2 2 0 0 1 2 2v18a2 2 0 0 1-2 2H7a2 2 0 0 1-2-2V3a2 2 0 0 1 2-2zm0 3v15h10V4zm5 16.2a1 1 0 1 0 0 .1z"/></svg>
        (407) 555-0168
      </li>
      <li class="contact-item">
        <svg viewBox="0 0 24 24"><path d="M6 2h12v5H6zM4 8h16a2 2 0 0 1 2 2v7h-4v5H6v-5H2v-7a2 2 0 0 1 2-2zm4 8v4h8v-4z"/></svg>
        (407) 555-0187
      </li>
      <li class="contact-item">
        <svg viewBox="0 0 24 24"><path d="M2 6l10 7 10-7v13H2zm0-2h20l-10 7z"/></svg>
        johndoe@dwelvano.com
      </li>
      <li class="contact-item">
        <svg viewBox="0 0 24 24"><path d="M12 2a10 10 0 1 0 0 20 10 10 0 0 0 0-20zm-1 17.9A8 8 0 0 1 4.2 10L9 15v1a2 2 0 0 0 2 2zm6.9-2.5A2 2 0 0 0 16 16h-1v-3a1 1 0 0 0-1-1H8v-2h2a1 1 0 0 0 1-1V7h2a2 2 0 0 0 2-2v-.4a8 8 0 0 1 2.9 12.8z"/></svg>
        dwelvano.com
      </li>
    </ul>

    <p class="address">48 Harbor Lane, Suite 210, Orlando, FL 32801</p>
  </section>

  <section class="card card-back">
    <div class="wordmark-back">Dwelvano</div>
    <p class="tagline">WE GUARD WHERE YOU LIVE</p>
    <p class="subline">A friendly local service</p>
  </section>
</body>
</html>
```